Bright Harbor Charity - helping the disadvantaged

I would like a new web site design for my charity BRIGHT HARBOR. The charity provides help for the disadvantaged. See current site
brightharbor.org.au for details. Please refer to the current site for information on the charity. The objectives of the charity are in the "about us" tab. You will also notice on the site that we provide information about events that we sponsor an area for this should be provided on the site.

Target Market(s)

We have two targets:
1. Individuals and Businesses that will donate money to the charity.
2. Individuals that are in need of support from the charity.

Industry/Entity Type

Charity

Requirements
Must have
• Ability for individuals to be able to understand the type of support we can provide.
Nice to have
• Our logo should be prominate on each pages
Should not have
• Should be use modern fonts

```html
<!DOCTYPE html>
<html lang="en">
<head>
<meta charset="utf-8">
<title>Bright Harbor – Helping the Disadvantaged</title>
<link href="https://fonts.googleapis.com/css2?family=Ubuntu:wght@400;500;700&display=swap" rel="stylesheet">
<style>
  :root {
    --bg-deep: #1b2527;
    --bg-glow: #3c4d50;
    --footer-bg: #151b1d;
    --panel-white: #ffffff;
    --panel-dark: #27353a;
    --text-dark: #1d1d1d;
    --text-body: #2b2b2b;
    --text-light: #e9eeee;
    --text-muted: #6d7a7d;
    --green: #5fae3c;
    --green-light: #7ccc52;
    --green-title: #7cc24f;
    --orange: #e8954a;
    --orange-light: #f3b472;
    --logo-green: #4f9a3a;
    --line: #2f3b3e;
  }
  * { box-sizing: border-box; margin: 0; padding: 0; }
  html, body { width: 942px; height: 1200px; overflow: hidden; }
  body {
    font-family: "Ubuntu", sans-serif;
    background:
      radial-gradient(ellipse 520px 420px at 470px 330px, var(--bg-glow), transparent 75%),
      var(--bg-deep);
    position: relative;
    color: var(--text-body);
  }
  .abs { position: absolute; }

  /* Navigation */
  .main-nav { left: 18px; top: 22px; display: flex; align-items: center; height: 26px; }
  .main-nav a { color: var(--text-light); text-decoration: none; font-size: 14px; padding: 0 24px; border-left: 1px solid #34504a; line-height: 18px; }
  .main-nav a.first { border-left: none; }
  .main-nav a.active {
    background: linear-gradient(var(--green-light), var(--green));
    color: #fff; border-radius: 4px; width: 90px; height: 26px; line-height: 26px;
    text-align: center; padding: 0; margin-right: 0;
  }

  /* Header panel */
  .header-panel { left: 18px; top: 63px; width: 904px; height: 395px; background: var(--panel-white); box-shadow: 0 3px 8px rgba(0,0,0,.5); }
  .brand { left: 14px; top: 27px; display: flex; align-items: center; gap: 8px; color: var(--logo-green); font-size: 27px; font-weight: 500; letter-spacing: .5px; }
  .brand-mark { width: 14px; height: 14px; background: var(--orange); border-radius: 50%; }
  .btn { top: 37px; height: 26px; border-radius: 4px; color: #fff; font-size: 15px; font-weight: 500; text-align: center; line-height: 26px; }
  .btn-donate { left: 710px; width: 93px; background: linear-gradient(var(--orange-light), var(--orange)); color: #3a2410; }
  .btn-login { left: 812px; width: 78px; background: linear-gradient(#3d4649, #1c2224); }
  .hero { left: 12px; top: 75px; width: 879px; height: 308px;
    background: radial-gradient(ellipse 300px 200px at 400px 150px, #8a8a8a, #3a3a3a 60%, #111 100%); }

  /* Content cards */
  .card { background: var(--panel-white); box-shadow: 0 3px 8px rgba(0,0,0,.5); }
  .card h2 { font-size: 21px; font-weight: 500; color: var(--text-dark); }
  .view-more { position: absolute; right: 19px; font-size: 10px; font-weight: 700; color: var(--text-dark); }
  .welcome { left: 30px; top: 484px; width: 562px; height: 202px; padding: 14px 18px; }
  .welcome p { margin-top: 12px; font-size: 10.6px; line-height: 18.4px; }
  .objectives { left: 30px; top: 699px; width: 562px; height: 202px; padding: 12px 20px; }
  .objectives h2 { font-size: 18px; }
  .objectives .lead { margin: 14px 0 4px 19px; font-size: 12px; font-weight: 700; }
  .objectives ul { list-style: none; }
  .objectives li { font-size: 11.3px; line-height: 23px; padding-left: 19px; position: relative; }
  .objectives li svg { position: absolute; left: 6px; top: 8px; }

  /* Announcements */
  .ann-head { left: 606px; top: 482px; width: 301px; height: 31px; background: var(--panel-white); padding: 4px 17px; font-size: 17px; font-weight: 500; color: var(--text-dark); }
  .ann-panel { left: 606px; top: 522px; width: 301px; height: 378px; background: var(--panel-dark); }
  .ann-item { position: absolute; left: 20px; width: 262px; }
  .ann-item h3 { font-size: 10.5px; font-weight: 500; color: var(--green-title); }
  .ann-item p { margin-top: 5px; font-size: 9.6px; line-height: 13.3px; color: var(--text-light); }
  .ann-img { width: 260px; height: 84px; margin-top: 8px; }
  .ann-more { text-align: right; font-size: 10px; font-weight: 700; color: #3a484c; margin-top: 3px; }
  .ann-divider { position: absolute; left: 0; top: 190px; width: 301px; height: 1px; background: #1d282b; }

  /* Footer */
  .footer { left: 0; top: 930px; width: 942px; height: 270px; background: var(--footer-bg); }
  .foot-links { top: 47px; list-style: none; }
  .foot-links li { font-size: 11.5px; line-height: 18.5px; color: #c9d1d2; }
  .foot-about { left: 303px; top: 48px; width: 280px; font-size: 10.4px; line-height: 13.8px; color: var(--text-muted); }
  .quick-title { left: 639px; top: 24px; font-size: 17px; font-weight: 500; color: #2a3538; }
  .field { left: 639px; border: 1px solid #4b5a5d; background: #121719; }
  .submit { left: 838px; top: 175px; width: 70px; height: 22px; background: var(--green); color: #fff; font-size: 11.5px; text-align: center; line-height: 22px; }
  .foot-rule { left: 16px; top: 216px; width: 906px; height: 1px; background: var(--line); }
  .copyright { left: 32px; top: 236px; font-size: 9.5px; color: #b9c2c3; }
</style>
</head>
<body>

<nav class="main-nav abs">
  <a class="active first" href="#">Home</a>
  <a class="first" href="#">About Us</a>
  <a href="#">Donate</a>
  <a href="#">Apply</a>
  <a href="#">Pledge</a>
  <a href="#">Nominate</a>
  <a href="#">Events</a>
  <a href="#">Directors</a>
  <a href="#">Contact Us</a>
</nav>

<header class="header-panel abs">
  <div class="brand abs"><span class="brand-mark"></span>BRIGHT HARBOR</div>
  <div class="btn btn-donate abs">Donate</div>
  <div class="btn btn-login abs">Login</div>
  <div class="hero abs" role="img" aria-label="Black and white photo of outstretched cupped hands holding copper coins"></div>
</header>

<section class="card welcome abs">
  <h2>Welcome to BRIGHT HARBOR</h2>
  <p>Lorem Ipsum is simply dummy text of the printing and typesetting industry. Lorem Ipsum has been the industry's standard dummy text ever since the 1500s, when an unknown printer took a galley of type and scrambled it to make a type specimen book. It has survived not only five centuries, but also the leap into electronic typesetting, remaining essentially unchanged. It was popularised in the 1960s with the release of Typeline sheets containing Lorem Ipsum passages, and more recently with desktop publishing software like Quillset Composer including versions of Lorem Ipsum.</p>
  <span class="view-more" style="top:176px">view more</span>
</section>

<section class="card objectives abs">
  <h2>Objectives</h2>
  <p class="lead">Providing direct assistance includes the following:</p>
  <ul>
    <li><svg width="7" height="8"><path d="M0 0L7 4L0 8Z" fill="#5fae3c"/></svg>Making loans to people in need;</li>
    <li><svg width="7" height="8"><path d="M0 0L7 4L0 8Z" fill="#5fae3c"/></svg>Providing training and education to people in need;</li>
    <li><svg width="7" height="8"><path d="M0 0L7 4L0 8Z" fill="#5fae3c"/></svg>Providing accommodation for people in medical care and their carers and families;</li>
    <li><svg width="7" height="8"><path d="M0 0L7 4L0 8Z" fill="#5fae3c"/></svg>Providing food to people in need; and</li>
    <li><svg width="7" height="8"><path d="M0 0L7 4L0 8Z" fill="#5fae3c"/></svg>Providing cash payments to people in need</li>
  </ul>
  <span class="view-more" style="top:177px">view more</span>
</section>

<div class="ann-head abs">Announcements</div>
<aside class="ann-panel abs">
  <div class="ann-item" style="top:9px">
    <h3>Kinship Day</h3>
    <p>Merrowvale's Inaugural Kinship Day Event 2012 Kinship Celebration Day – "EVERYONE BELONGS" Date: Saturday 24th March 2012 Venue: Linden Care Learning Centre, Ashcombe Road, Tallowood. ....</p>
    <div class="ann-img" role="img" aria-label="Event banner with a row of colourful paper-chain people on black" style="background:linear-gradient(#0c0c0c 45%, #2d2a18 70%, #4a3a5e)"></div>
    <div class="ann-more">read more</div>
  </div>
  <div class="ann-divider"></div>
  <div class="ann-item" style="top:197px">
    <h3>Art Exhibition</h3>
    <p>Calling on all local artists, sculptures and photographers the "Everyone Belongs" Art Exhibition will be held in conjunction with Kinship Day celebrations 22 – 24 March 2012 at Linden Care Learning Centre......</p>
    <div class="ann-img" role="img" aria-label="Dot painting artwork in red, orange and cream tones" style="height:85px;background:radial-gradient(circle at 50% 50%, #c9a37a, #8c2a1c 35%, #b55a24 60%, #5c1c16)"></div>
    <div class="ann-more">read more</div>
  </div>
</aside>

<footer class="footer abs">
  <ul class="foot-links abs" style="left:31px">
    <li>Home</li><li>About Us</li><li>Donate</li><li>Apply</li><li>Pledge</li>
  </ul>
  <ul class="foot-links abs" style="left:157px;top:48px">
    <li>Nominate</li><li>Events</li><li>Contact Us</li><li>Directors</li>
  </ul>
  <p class="foot-about abs">Lorem Ipsum is simply dummy text of the printing and typesetting industry. Lorem Ipsum has been the industry's standard dummy text ever since the 1500s, when an unknown printer took a galley of type and scrambled it to make a type specimen book. It has survived not only five centuries, but also the leap into electronic typesetting, remaining essentially unchanged.</p>
  <div class="quick-title abs">Quick Mail</div>
  <div class="field abs" style="top:49px;width:269px;height:25px"></div>
  <div class="field abs" style="top:81px;width:269px;height:87px"></div>
  <div class="submit abs">Submit</div>
  <div class="foot-rule abs"></div>
  <p class="copyright abs">Copyright © 2012 Bright Harbor Proprietary Limited. All Rights Reserved.</p>
</footer>

</body>
</html>
```